Custom unique Stationary design for Logistics company

We need a custom, unique , elegant and luxurious full stationary design using our new logo, following these guidelines:
1- Business card: double sided, both sides uses the navy blue as the background main color (same as the code of the navy blue used in our logo).
2- envelope and folder: also use the same navy blue as the main background color.
3- book cover( notepad cover) : same thing with the navy blue
4- letterhead: feel free to use the combination of the colors in our logo.
5- rest of the items are up to your creativity

Target Market(s)

corporates and other businesses

Industry/Entity Type

Logistics and heavy machines contractors

Requirements
Must have
• Letterhead, business card, envelope, notepad cover, paper, file
Nice to have
• navy blue to be main background color for business card, envelope, notepad cover

```html
<!DOCTYPE html>
<html lang="en">
<head>
<meta charset="utf-8">
<title>Meridian Haulage Group – Business Card</title>
<link rel="stylesheet" href="https://fonts.googleapis.com/css2?family=Roboto:wght@400;700&display=swap">
<style>
  :root {
    --stage: #3b3b3b;
    --navy: #0e4e74;
    --navy-deep: #0a3f60;
    --white: #ffffff;
    --orange: #f05a22;
    --muted: #b9c7d2;
  }
  * { box-sizing: border-box; margin: 0; padding: 0; }
  html, body { width: 1200px; height: 900px; overflow: hidden; }
  body {
    background: var(--stage);
    font-family: "Roboto", Arial, sans-serif;
    display: flex;
    align-items: center;
    justify-content: center;
    gap: 40px;
  }
  .card {
    width: 540px;
    height: 310px;
    border-radius: 20px;
    background: linear-gradient(160deg, var(--navy) 0%, var(--navy-deep) 100%);
    color: var(--white);
    position: relative;
  }
  .wordmark {
    display: flex;
    align-items: center;
    gap: 12px;
  }
  .wordmark-dot {
    width: 14px; height: 14px;
    border-radius: 50%;
    background: var(--orange);
    flex: none;
  }
  .wordmark-name {
    font-weight: 700;
    color: var(--white);
    line-height: 1.05;
    letter-spacing: 1px;
  }

  /* Logo side */
  .card-back {
    display: flex;
    align-items: center;
    justify-content: center;
  }
  .card-back .wordmark-name { font-size: 40px; }
  .card-back .wordmark-dot { width: 20px; height: 20px; }

  /* Contact side */
  .card-front {
    display: flex;
    align-items: center;
    padding: 0 30px;
  }
  .card-front .brand {
    width: 200px;
    display: flex;
    justify-content: center;
  }
  .card-front .wordmark-name { font-size: 22px; }
  .divider {
    width: 1px;
    height: 190px;
    background: var(--white);
    margin: 0 24px;
    opacity: 0.85;
  }
  .details { font-size: 14px; line-height: 1.45; }
  .person-name {
    color: var(--orange);
    font-weight: 700;
    font-size: 17px;
    text-transform: uppercase;
  }
  .person-role { font-weight: 700; font-size: 15px; margin-bottom: 10px; }
  .address { margin-bottom: 6px; }
  .contact-list { list-style: none; }
  .contact-list li { display: flex; align-items: center; gap: 8px; }
  .contact-list svg { width: 13px; height: 13px; flex: none; }
</style>
</head>
<body>

  <section class="card card-front">
    <div class="brand">
      <div class="wordmark">
        <span class="wordmark-dot"></span>
        <span class="wordmark-name">MERIDIAN<br>HAULAGE</span>
      </div>
    </div>
    <div class="divider"></div>
    <div class="details">
      <p class="person-name">Elio Marchetti</p>
      <p class="person-role">Managing Director</p>
      <p class="address">Via dei Tralci 14/A<br>Borgo Alto(BA) 70123</p>
      <ul class="contact-list">
        <li>
          <svg viewBox="0 0 16 16" fill="var(--orange)"><path d="M3.6 1.2l2.3 2.6-1.3 1.7c.9 2 2.4 3.6 4.4 4.5l1.7-1.3 2.6 2.3-1.2 2.5C6.6 13.4 2.6 9.4 1.1 3.9z"/></svg>
          <span>0000/555012</span>
        </li>
        <li>
          <svg viewBox="0 0 16 16" fill="var(--orange)"><rect x="1" y="3" width="14" height="10" rx="1"/><path d="M1.5 3.6L8 9l6.5-5.4" stroke="var(--navy)" stroke-width="1.4" fill="none"/></svg>
          <span>info@meridianhaulage.it</span>
        </li>
        <li>
          <svg viewBox="0 0 16 16" fill="none" stroke="var(--orange)" stroke-width="1.5"><circle cx="8" cy="8" r="6.5"/><ellipse cx="8" cy="8" rx="3" ry="6.5"/><path d="M1.5 8h13"/></svg>
          <span>www.meridianhaulage.it</span>
        </li>
      </ul>
    </div>
  </section>

  <section class="card card-back">
    <div class="wordmark">
      <span class="wordmark-dot"></span>
      <span class="wordmark-name">MERIDIAN<br>HAULAGE</span>
    </div>
  </section>

</body>
</html>
```